RM Installations Web Site Design

Need a basic site to show clients a little about what we do. We are a custom audio video company in the high-end residential market. Need a few basic but professional pages to show past projects and products we sell. No e-commerce. Should include my new logo from MarkBazaar.

Industry/Entity Type

Residential

Number of Pages Required

2 page

Font styles to use
Serif
Sans Serif

Colors
f78f20

Requirements
Must have
• Company Logo, Send feedback page
Nice to have
• I have no ideas about design, but I do know what I like and dislike when I see it.

```html
<!DOCTYPE html>
<html lang="en">
<head>
<meta charset="utf-8">
<title>RM Installations – Custom Audio Video</title>
<link href="https://fonts.googleapis.com/css2?family=Roboto:wght@300;400;500&display=swap" rel="stylesheet">
<style>
:root{
  --orange:#f78f20;
  --dark:#333;
  --text:#555;
  --panel:#e4e5e3;
  --line:#cfcfcf;
  --white:#fff;
}
*{box-sizing:border-box;margin:0;padding:0}
html,body{width:950px;height:1200px;overflow:hidden;background:var(--white);font-family:'Roboto',sans-serif;color:var(--text)}
.page{position:relative;width:950px;height:1200px}
.topline{position:absolute;top:0;left:0;width:950px;height:4px;background:#e9e9e9}
.phone-tab{position:absolute;left:749px;top:4px;width:143px;height:33px;background:#e6e6e6;border-radius:0 0 3px 3px;display:flex;align-items:center;justify-content:center;gap:7px;font-size:11.5px;font-weight:500;color:var(--dark)}
.phone-tab span{color:var(--orange)}
.brand{position:absolute;left:59px;top:34px;display:flex;align-items:center;gap:8px}
.brand-mark{width:34px;height:34px;background:var(--orange)}
.brand-name{font-size:16px;font-weight:400;color:var(--dark);line-height:1}
.nav{position:absolute;top:52px;right:58px;display:flex;align-items:center;gap:0}
.nav a{font-size:11.5px;color:var(--dark);text-decoration:none;padding:0 12px;line-height:27px}
.nav a.active{background:var(--orange);color:var(--white);border-radius:2px;font-weight:500;margin-right:1px}
.hero{position:absolute;top:85px;left:0;width:950px;height:345px;background:linear-gradient(180deg,#7d6c66 0%,#a7958c 45%,#c9bdb2 100%)}
.hero-title{position:absolute;top:122px;left:0;width:950px;text-align:center;font-size:30px;font-weight:300;color:var(--white);line-height:37px}
.hero-btn{position:absolute;left:423px;top:208px;width:104px;height:34px;background:var(--orange);color:var(--white);font-size:11.5px;display:flex;align-items:center;justify-content:center;border-radius:2px}
.dots{position:absolute;top:312px;left:442px;display:flex;gap:6px}
.dots i{width:12px;height:12px;border-radius:50%;background:var(--white)}
.dots i:first-child{background:var(--orange)}
.h2{color:var(--orange);font-size:18px;font-weight:400}
.welcome{position:absolute;left:59px;top:458px;width:548px}
.welcome p{font-size:10.3px;line-height:17.5px;margin-top:8px;font-weight:300;color:#444}
.welcome .h2{margin-bottom:2px}
.btn-dark{display:inline-flex;align-items:center;justify-content:center;height:29px;padding:0 13px;background:#333;color:var(--white);font-size:10.5px;border-radius:2px}
.welcome .btn-dark{margin-top:19px}
.divider{position:absolute;left:59px;top:700px;width:548px;height:1px;background:var(--line)}
.services-head{position:absolute;left:59px;top:724px;width:548px;display:flex;justify-content:space-between;align-items:baseline}
.services-head small{font-size:9.5px;color:var(--orange);font-weight:500;letter-spacing:.3px}
.service{position:absolute;width:173px}
.service .photo{height:111px}
.service p{font-size:12px;color:var(--dark);margin-top:14px}
.panel{position:absolute;left:629px;width:263px;background:var(--panel);padding:14px}
.panel h3{font-size:17.5px;font-weight:400;color:var(--dark)}
.products{top:461px;height:284px}
.arrows{position:absolute;right:16px;top:18px}
.product-img{margin:12px 0 0 -1px;width:234px;height:106px;background:linear-gradient(135deg,#f2f2f2,#c9cfd8)}
.product-body{padding-left:2px}
.item-h{font-size:13.5px;color:var(--orange);margin-top:12px}
.item-p{font-size:10.3px;line-height:17px;font-weight:300;color:#444;margin-top:2px}
.products .btn-dark{margin-top:9px}
.projects{top:769px;height:283px}
.project{display:flex;gap:14px;margin-top:14px}
.project:first-of-type{margin-top:13px}
.project .thumb{width:75px;height:62px;flex:none}
.project .item-h{margin-top:-3px}
.project .item-p{font-size:10px;line-height:15px}
.footer{position:absolute;left:0;top:1090px;width:950px;height:110px;background:var(--orange);color:var(--white)}
.footer nav{position:absolute;left:60px;top:24px;display:flex;gap:22px;font-size:10.5px;font-weight:500}
.footer .legal{position:absolute;left:60px;top:61px;font-size:9.5px;line-height:19px}
.connect{position:absolute;left:758px;top:21px;font-size:10.5px}
.social{display:flex;gap:13px;margin-top:10px}
.social i{width:24px;height:24px;border-radius:50%;background:var(--white)}
</style>
</head>
<body>
<div class="page">
  <div class="topline"></div>
  <div class="phone-tab">
    <svg width="13" height="13" viewBox="0 0 13 13"><rect width="13" height="13" rx="2" fill="#666"/><path d="M4 3.5c0 3 2 5.5 5 6l1-1.3-1.5-1-0.8.7c-1-.5-1.8-1.3-2.2-2.3l.7-.8-1-1.5z" fill="#e6e6e6"/></svg>
    PH: <span>555-014-2288</span>
  </div>
  <div class="brand"><div class="brand-mark"></div><div class="brand-name">RM INSTALLATIONS</div></div>
  <nav class="nav">
    <a class="active">Home</a><a>About Us</a><a>Services</a><a>Products</a><a>Recent Projects</a><a>Contact Us</a>
  </nav>

  <section class="hero" role="img" aria-label="Photo of a home theatre room with speakers, screen and cream sofas">
    <h1 class="hero-title" style="font-weight:300">We are a custom audio video company in<br>the high-end residential market.</h1>
    <div class="hero-btn">CONTACT US</div>
    <div class="dots"><i></i><i></i><i></i><i></i></div>
  </section>

  <section class="welcome">
    <h2 class="h2">Welcome to Our Website</h2>
    <p>Aliquam molestie, mi et imperdiet euismod, dui purus auctor tellus, et interdum lacus lectus et ante. Sed accumsan sollicitudin sapien, sit amet adipiscing turpis gravida ac. In congue, neque ac lobortis volutpat, libero mauris varius mi, vitae suscipit ipsum ligula vitae risus. Duis aliquam nibh a dui iaculis viverra id a velit. Vivamus egestas risus in magna varius commodo. Sed semper viverra egestas. Etiam pretium porttitor lectus, vel ornare neque porta volutpat.</p>
    <p style="margin-top:4px">Aenean a nibh eget turpis vehicula tempus ac sed massa. Vestibulum dolor nulla, ultrices ac tincidunt sed, laoreet non est. Suspendisse lobortis turpis in odio blandit ac interdum lorem euismod. Etiam risus massa, vulputate eu pellentesque et, consectetur a neque.</p>
    <div class="btn-dark">READ MORE</div>
  </section>
  <div class="divider"></div>

  <div class="services-head"><h2 class="h2">Our Services</h2><small>VIEW ALL SERVICES</small></div>
  <div class="service" style="left:59px;top:760px"><div class="photo" role="img" aria-label="Photo of a hand touching a wall audio keypad" style="background:linear-gradient(90deg,#c9c9c9,#e8e8e8 50%,#7f93b5)"></div><p>Distributed Audio/Video</p></div>
  <div class="service" style="left:247px;top:760px"><div class="photo" role="img" aria-label="Photo of a residential cinema room" style="background:linear-gradient(180deg,#8a7d74,#d8cfc4)"></div><p>Residential Cinemas</p></div>
  <div class="service" style="left:434px;top:760px"><div class="photo" role="img" aria-label="Photo of a touch panel and smartphone controller" style="background:linear-gradient(90deg,#dfe2e4,#8fa7c2 60%,#34508a)"></div><p>Whole-House Control Systems</p></div>
  <div class="service" style="left:59px;top:919px"><div class="photo" role="img" aria-label="Photo of a white security camera" style="background:linear-gradient(135deg,#a59c8f,#e5e2dc 55%,#8a8f86)"></div><p style="margin-top:11px">Security Camera Systems</p></div>
  <div class="service" style="left:247px;top:919px"><div class="photo" role="img" aria-label="Photo of a media room with red seating" style="background:linear-gradient(180deg,#4a3128,#8a5048 60%,#b96e63)"></div><p>Media Rooms</p></div>
  <div class="service" style="left:434px;top:919px"><div class="photo" role="img" aria-label="Photo of an outdoor movie screen in a garden at dusk" style="background:linear-gradient(180deg,#3a4a6a,#6a7a8a 50%,#2d4a2a)"></div><p>Outdoor Audio and Video</p></div>

  <aside class="panel products">
    <h3>Our Products</h3>
    <svg class="arrows" width="26" height="12" viewBox="0 0 26 12"><path d="M6 1L1 6l5 5M20 1l5 5-5 5" fill="none" stroke="#333" stroke-width="1.3"/></svg>
    <div class="product-img" role="img" aria-label="Product photo of speakers and a flat-screen television"></div>
    <div class="product-body">
      <div class="item-h">Product Heading</div>
      <div class="item-p">Aliquam molestie, mi et imperdiet euismod, dui purus auctor tellus, et interdum lacus lectus et ante risus in magna varius..</div>
      <div class="btn-dark">READ MORE</div>
    </div>
  </aside>

  <aside class="panel projects">
    <h3>Recent Projects</h3>
    <div class="project"><div class="thumb" role="img" aria-label="Project photo of a dark home cinema with orange seats" style="background:linear-gradient(180deg,#2a2a2a,#9a5a2a)"></div><div><div class="item-h">Project Heading</div><div class="item-p">Aliquam molestie, mi et imperdiet euismod, dui purus auctor tellus..</div></div></div>
    <div class="project"><div class="thumb" role="img" aria-label="Project photo of a bright living room with orange sofa" style="background:linear-gradient(180deg,#e8e8e8,#c86a3a)"></div><div><div class="item-h">Project Heading</div><div class="item-p">Aliquam molestie, mi et imperdiet euismod, dui purus auctor tellus..</div></div></div>
    <div class="project"><div class="thumb" role="img" aria-label="Project photo of a media room with large screen" style="background:linear-gradient(180deg,#3a3228,#5a6a3a 50%,#1e1e1e)"></div><div><div class="item-h">Project Heading</div><div class="item-p">Aliquam molestie, mi et imperdiet euismod, dui purus auctor tellus..</div></div></div>
  </aside>

  <footer class="footer">
    <nav><span>Home</span><span>About Us</span><span>Services</span><span>Products</span><span>Recent Projects</span><span>Contact Us</span></nav>
    <div class="legal">Copyright © 2015 RM Installations LLC.All Right Reserved<br>License: 0284406-B2</div>
    <div class="connect">Connect Us<div class="social"><i></i><i></i><i></i><i></i></div></div>
  </footer>
</div>
</body>
</html>
```